Business Card for beauty technology startup

Design Glimora Business Card for a Beauty, based on the website identity and colors (https://www.glimora-example.com).
Glimora is a beauty tech startup that gathers helpful product info for beauty lovers and consumers (such as availability on stores, price range and product reviews) for makeup products. The card design must be young, colorful but clean, and very modern.

Target Market(s)

woman, 15-35

Industry/Entity Type

Cosmetics

Contact Information for Business Card

Full Name, address, phone

Font styles to use
Other font styles liked:
• Advent Pro

Colors
e34297
86cfc6
ffffff
5c5c5c
e8e8e8
e667a6
b2b2b2

Requirements
Must have
• One full colored side with a creative design and another with card info
• Use Color palette: #95C5C5 and/or #D38AA5
• Use fonts: Advent Pro
• Use website identity: https://www.glimora-example.com
Nice to have
• If needed extra font: Roboto

```html
<!DOCTYPE html>
<html lang="en">
<head>
<meta charset="utf-8">
<title>Glimora Business Card</title>
<link href="https://fonts.googleapis.com/css2?family=Advent+Pro:wght@300;400;600&family=Abel&display=swap" rel="stylesheet">
<style>
  :root {
    --bg: #e6e6e6;
    --rose: #c97e98;
    --rose-deep: #b97290;
    --rose-text: #c06a8c;
    --teal: #86c5c3;
    --paper: #f4f4f2;
    --ink: #2e2a2c;
    --white: #ffffff;
  }
  * { margin: 0; padding: 0; box-sizing: border-box; }
  html, body { width: 1200px; height: 576px; overflow: hidden; background: var(--bg); }
  .canvas { position: relative; width: 1200px; height: 576px; }
  .card {
    position: absolute; width: 486px; height: 294px; top: 138px;
    border-radius: 13px; overflow: hidden;
  }
  .card-front { left: 82px; background: linear-gradient(180deg, var(--rose) 0%, var(--rose-deep) 100%); }
  .card-back { left: 602px; background: var(--paper); }
  .brand { position: absolute; display: flex; align-items: center; gap: 24px; }
  .brand-dot { width: 66px; height: 66px; border-radius: 50%; border: 1.5px solid currentColor; flex: none; }
  .brand-name {
    font-family: "Advent Pro", sans-serif; font-weight: 300;
    font-size: 48px; letter-spacing: 6px; line-height: 1;
  }
  .card-front .brand { left: 104px; top: 108px; color: var(--ink); }
  .card-back .brand { left: 32px; top: 97px; color: var(--rose-text); }
  .top-band {
    position: absolute; left: 0; top: 0; width: 100%; height: 66px;
    background: var(--rose);
  }
  .top-rule {
    position: absolute; left: 0; top: 72px; width: 100%; height: 5px;
    background: var(--teal);
  }
  .holder-name {
    position: absolute; right: 34px; top: 22px; color: var(--white);
    font-family: "Advent Pro", sans-serif; font-weight: 600; font-size: 22px; letter-spacing: 0.5px; line-height: 1;
  }
  .address, .contacts {
    position: absolute; font-family: "Abel", sans-serif; font-size: 12.5px;
    line-height: 16px; color: var(--rose-text);
  }
  .address { left: 32px; top: 226px; font-style: normal; }
  .contacts { right: 34px; top: 212px; list-style: none; text-align: right; }
  .contacts li { display: flex; justify-content: flex-end; align-items: center; gap: 11px; }
  .contacts svg { width: 12px; height: 12px; stroke: var(--teal); fill: none; stroke-width: 1.4; }
</style>
</head>
<body>
<main class="canvas">
  <section class="card card-front">
    <div class="brand">
      <span class="brand-dot"></span>
      <span class="brand-name">GLIMORA</span>
    </div>
  </section>

  <section class="card card-back">
    <div class="top-band"></div>
    <div class="top-rule"></div>
    <h2 class="holder-name">MARA QUINN</h2>
    <div class="brand">
      <span class="brand-dot"></span>
      <span class="brand-name">GLIMORA</span>
    </div>
    <address class="address">48, Lumen Avenue, Brightvale,<br>Solaria - 904512</address>
    <ul class="contacts">
      <li>00 555 010 777
        <svg viewBox="0 0 12 12"><path d="M2.5 1.5 L4.5 1.5 L5.2 3.8 L4 4.8 C4.6 6.2 5.8 7.4 7.2 8 L8.2 6.8 L10.5 7.5 L10.5 9.5 C6 10 2 6 2.5 1.5 Z"/></svg></li>
      <li>www.glimora-example.com
        <svg viewBox="0 0 12 12"><path d="M5 7 L7 5 M4.5 5.5 L2.8 7.2 A1.6 1.6 0 0 0 4.8 9.2 L6.5 7.5 M7.5 6.5 L9.2 4.8 A1.6 1.6 0 0 0 7.2 2.8 L5.5 4.5"/></svg></li>
      <li>yourname@glimora-example.com
        <svg viewBox="0 0 12 12"><rect x="1.5" y="3" width="9" height="6.5"/><path d="M1.5 3 L6 6.8 L10.5 3"/></svg></li>
    </ul>
  </section>
</main>
</body>
</html>
```